Australian Trucking Company Requires Professional Looking Stationary

We require a professional looking stationary design that incorporates our newly designed logo.

Our business, called "Brell Haulage Contracting", provides contracting work, transport and logistics to business in Western Australia particularly with links to the mining sector.

We are a small business looking to expand and our new logo and our new stationary will help develop our brand image in our market place.

Target Market(s)

Businesses and Corporation with links to the Mining Sector

Industry/Entity Type

Small Business

Requirements
Must have
• The letterhead must have the following details:
The new logo

Text saying: "Brell Holdings Pty Ltd (ACN 582 316 907) ATF The Brell Discretionary Trust T/AS"
"ABN 71 834 209 553"
Address "P.O Box 817 Wattlegrove WA, 6958"
Phone: 08 9352 7140
Email: brellhaul@mailbox-example.com.au

The text on the letterhead should be editable as the details are likely to change in the near future. Provision should be made for a website address all though one isn't available at the moment.

The styling, layout and font text is entirely up to the designer.

```html
<!DOCTYPE html>
<html lang="en">
<head>
<meta charset="utf-8">
<title>Brell Haulage Contracting – Business Card</title>
<link href="https://fonts.googleapis.com/css2?family=Open+Sans:wght@400;600;700&display=swap" rel="stylesheet">
<style>
  :root {
    --red: #e31e24;
    --red-deep: #c3161c;
    --red-light: #ee2a2f;
    --white: #ffffff;
    --ink: #2b2b2b;
    --grey: #5a5a5a;
    --page: #efefef;
  }
  * { margin: 0; padding: 0; box-sizing: border-box; }
  html, body { width: 1200px; height: 650px; overflow: hidden; }
  body {
    background: var(--page);
    font-family: "Open Sans", Arial, sans-serif;
    position: relative;
  }
  .card {
    position: absolute;
    top: 170px;
    width: 540px;
    height: 310px;
    border-radius: 22px;
    overflow: hidden;
    box-shadow: 0 6px 18px rgba(0,0,0,0.18);
  }
  /* Front */
  .card-front { left: 40px; background: var(--white); }
  .brand {
    position: absolute;
    left: 48px;
    top: 40px;
    display: flex;
    align-items: center;
    gap: 22px;
  }
  .brand-square {
    width: 54px; height: 54px;
    background: var(--grey);
  }
  .brand-name {
    color: var(--red);
    font-weight: 700;
    font-size: 30px;
    line-height: 1.05;
    text-transform: uppercase;
    letter-spacing: 0.5px;
  }
  .contact-band {
    position: absolute;
    left: 0; right: 0;
    top: 150px;
    height: 104px;
    background: var(--red);
    color: var(--white);
  }
  .person {
    position: absolute;
    right: 312px;
    top: 32px;
    text-align: right;
  }
  .person-name { font-weight: 700; font-size: 16px; line-height: 1.2; }
  .person-title { font-size: 13px; line-height: 1.3; }
  .divider {
    position: absolute;
    left: 240px;
    top: 18px;
    width: 1px;
    height: 68px;
    background: var(--white);
  }
  .contact-list {
    position: absolute;
    left: 254px;
    top: 20px;
    list-style: none;
    font-size: 12.5px;
    line-height: 21px;
  }
  .contact-list li { display: flex; align-items: center; gap: 7px; }
  .contact-list svg { width: 11px; height: 11px; fill: var(--white); flex: none; }
  .address {
    position: absolute;
    left: 0; right: 0;
    top: 254px;
    height: 56px;
    display: flex;
    align-items: center;
    justify-content: center;
    font-size: 14px;
    letter-spacing: 0.6px;
    color: var(--ink);
  }
  /* Back */
  .card-back {
    left: 620px;
    background: linear-gradient(160deg, var(--red-deep) 0%, var(--red) 45%, var(--red-light) 100%);
    color: var(--white);
    text-align: center;
  }
  .back-brand {
    position: absolute;
    left: 0; right: 0;
    top: 62px;
    font-weight: 700;
    font-size: 30px;
    line-height: 1.1;
    text-transform: uppercase;
    letter-spacing: 0.5px;
  }
  .back-web {
    position: absolute;
    left: 0; right: 0;
    top: 178px;
    font-size: 24px;
    font-weight: 600;
    letter-spacing: 0.5px;
  }
  .legal {
    position: absolute;
    left: 20px; right: 20px;
    top: 226px;
    font-size: 11.5px;
    line-height: 20px;
  }
</style>
</head>
<body>
  <section class="card card-front" aria-label="Business card front">
    <div class="brand">
      <div class="brand-square"></div>
      <div class="brand-name">Brell Haulage<br>Contracting</div>
    </div>
    <div class="contact-band">
      <div class="person">
        <div class="person-name">Your Name</div>
        <div class="person-title">Title</div>
      </div>
      <div class="divider"></div>
      <ul class="contact-list">
        <li><svg viewBox="0 0 24 24"><path d="M6.6 10.8a15.1 15.1 0 0 0 6.6 6.6l2.2-2.2a1 1 0 0 1 1-.25 11.4 11.4 0 0 0 3.6.57 1 1 0 0 1 1 1V20a1 1 0 0 1-1 1A17 17 0 0 1 3 4a1 1 0 0 1 1-1h3.5a1 1 0 0 1 1 1c0 1.25.2 2.45.57 3.57a1 1 0 0 1-.25 1z"/></svg>08 9352 7140</li>
        <li><svg viewBox="0 0 24 24"><path d="M2 5h20v14H2z M2 5l10 8 10-8" /></svg>brellhaul@mailbox-example.com.au</li>
        <li><svg viewBox="0 0 24 24"><circle cx="12" cy="12" r="10"/></svg>www.brellhaulage.com</li>
      </ul>
    </div>
    <div class="address">P.O Box 817 Wattlegrove WA, 6958</div>
  </section>

  <section class="card card-back" aria-label="Business card back">
    <div class="back-brand">Brell Haulage<br>Contracting</div>
    <div class="back-web">www.brellhaulage.com</div>
    <div class="legal">
      Brell Holdings Pty Ltd (ACN 582 316 907) ATF The Brell Discretionary Trust T/AS<br>
      ABN 71 834 209 553
    </div>
  </section>
</body>
</html>
```